Business Card for Professional Photographer

I'm looking for an eye catching modern clean design that compliments my logo/ website fonts & colours.
I specialise in architecture, corporate & commercial photography so I'm marketing to professional clients rather than portrait / wedding clients.

I would prefer to not have a solid black design.

My logo brand guide is as follows :

Main front font. : Reislust
Main font colour : #fff
Slogan front font : Ubuntu Bold
Monogram front font : Venti Medium
Container colour : #fff

I need print ready files in pdf .png & .eps formats.

Included in the files below are some screen grabs as reference to font & colours etc.

```html
<!DOCTYPE html>
<html lang="en">
<head>
<meta charset="utf-8">
<title>Clear Angle – Business Card</title>
<link rel="stylesheet" href="https://fonts.googleapis.com/css2?family=Ubuntu:wght@300;400;700&family=Roboto:wght@400&family=Fjalla+One&display=swap">
<style>
  :root {
    --backdrop: #c9c9c9;
    --card-dark: #151515;
    --card-dark-2: #262420;
    --card-light: #f4f4f4;
    --gold: #c29a52;
    --gold-light: #e3c682;
    --gold-deep: #a87d35;
    --ink: #2b2b2b;
    --ink-soft: #444444;
    --ghost: #e4e4e4;
  }
  * { box-sizing: border-box; margin: 0; padding: 0; }
  html, body { width: 1200px; height: 576px; overflow: hidden; }
  body { background: var(--backdrop); position: relative; font-family: "Roboto", sans-serif; }

  .card {
    position: absolute;
    top: 138px;
    width: 484px;
    height: 294px;
    border-radius: 10px;
    overflow: hidden;
  }

  /* Front */
  .card--front { left: 82px; background: var(--card-dark); }
  .front__collage {
    position: absolute; inset: 0;
    background: linear-gradient(135deg, var(--card-dark-2) 0%, var(--card-dark) 55%, #1d1f22 100%);
  }
  .front__mark {
    position: absolute; left: 106px; top: 112px;
    width: 52px; height: 52px;
    border: 3px solid var(--gold); border-radius: 50%;
  }
  .front__name {
    position: absolute; left: 182px; top: 118px;
    font-family: "Ubuntu", sans-serif; font-weight: 300;
    font-size: 22px; letter-spacing: 3.4px; color: var(--gold);
  }
  .front__tagline {
    position: absolute; left: 184px; top: 150px;
    font-family: "Ubuntu", sans-serif; font-weight: 700;
    font-size: 7.5px; letter-spacing: 1.6px; color: var(--gold);
  }
  .front__web {
    position: absolute; left: 0; right: 0; top: 256px;
    text-align: center;
    font-family: "Ubuntu", sans-serif; font-weight: 300;
    font-size: 13px; letter-spacing: 2px; color: var(--gold-light);
  }

  /* Back */
  .card--back { left: 602px; background: var(--card-light); }
  .back__ghost {
    position: absolute; right: -40px; top: 70px;
    width: 150px; height: 150px;
    border: 14px solid var(--ghost); border-radius: 50%;
  }
  .back__mark {
    position: absolute; left: 104px; top: 76px;
    width: 56px; height: 56px;
    border: 3px solid var(--gold); border-radius: 50%;
  }
  .back__brand {
    position: absolute; left: 38px; width: 186px; top: 172px;
    text-align: center;
    font-family: "Ubuntu", sans-serif; font-weight: 300;
    font-size: 17px; letter-spacing: 2.6px; color: var(--gold);
  }
  .back__tagline {
    position: absolute; left: 38px; width: 186px; top: 196px;
    text-align: center;
    font-family: "Ubuntu", sans-serif; font-weight: 700;
    font-size: 6px; letter-spacing: 1.2px; color: var(--gold);
  }
  .person { position: absolute; left: 269px; top: 76px; }
  .person__name {
    font-family: "Fjalla One", sans-serif; font-size: 18px;
    color: var(--gold-deep); line-height: 1.2;
  }
  .person__role { font-size: 12.5px; color: var(--ink-soft); margin-top: 1px; }
  .contact { position: absolute; left: 269px; top: 132px; list-style: none; }
  .contact__item {
    display: flex; align-items: center; gap: 12px;
    font-size: 12.5px; color: var(--ink); height: 18.5px;
  }
  .contact__icon { width: 11px; height: 11px; flex: none; }
  .back__strip {
    position: absolute; left: 0; bottom: 0; width: 240px; height: 10px;
    background: linear-gradient(90deg, var(--card-light) 0%, var(--gold-light) 45%, var(--gold) 100%);
  }
  .back__band { position: absolute; right: 0; bottom: 0; width: 268px; height: 36px; }
  .back__address {
    position: absolute; right: 26px; bottom: 11px;
    font-size: 12.5px; color: var(--ink);
  }
</style>
</head>
<body>

<section class="card card--front">
  <div class="front__collage" role="img" aria-label="Darkened collage of architecture and commercial photographs"></div>
  <div class="front__mark"></div>
  <div class="front__name">CLEAR ANGLE</div>
  <div class="front__tagline">Architecture Corporate Commercial</div>
  <div class="front__web">www.clearangle.com.au</div>
</section>

<section class="card card--back">
  <div class="back__ghost"></div>
  <div class="back__mark"></div>
  <div class="back__brand">CLEAR ANGLE</div>
  <div class="back__tagline">Architecture Corporate Commercial</div>

  <div class="person">
    <div class="person__name">Adrian Hale</div>
    <div class="person__role">Photographer</div>
  </div>

  <ul class="contact">
    <li class="contact__item">
      <svg class="contact__icon" viewBox="0 0 12 12"><path d="M2 1h2.5l1 3-1.5 1a6 6 0 0 0 3 3l1-1.5 3 1V10a1 1 0 0 1-1 1A9 9 0 0 1 1 2a1 1 0 0 1 1-1z" fill="var(--gold)"/></svg>
      0400718265
    </li>
    <li class="contact__item">
      <svg class="contact__icon" viewBox="0 0 12 12"><rect x="0.5" y="2.5" width="11" height="7" fill="var(--gold)"/><path d="M0.5 2.5 6 6.5l5.5-4" fill="none" stroke="var(--card-light)" stroke-width="1"/></svg>
      info@clearangle.com.au
    </li>
    <li class="contact__item">
      <svg class="contact__icon" viewBox="0 0 12 12"><circle cx="6" cy="6" r="5" fill="none" stroke="var(--gold)" stroke-width="1.2"/><ellipse cx="6" cy="6" rx="2.2" ry="5" fill="none" stroke="var(--gold)" stroke-width="1"/><line x1="1" y1="6" x2="11" y2="6" stroke="var(--gold)" stroke-width="1"/></svg>
      www.clearangle.com.au
    </li>
  </ul>

  <div class="back__strip"></div>
  <svg class="back__band" viewBox="0 0 268 36" preserveAspectRatio="none">
    <defs>
      <linearGradient id="bandGold" x1="0" x2="1" y1="0" y2="0">
        <stop offset="0" stop-color="var(--gold)"/>
        <stop offset="0.5" stop-color="var(--gold-light)"/>
        <stop offset="1" stop-color="var(--gold)"/>
      </linearGradient>
    </defs>
    <path d="M22 0H268V36H0Z" fill="url(#bandGold)"/>
  </svg>
  <div class="back__address">48 Quarry Rd Beaufort Vic 3373</div>
</section>

</body>
</html>
```